Business card alterations

I have changed my business name from Brisa Laser Renewal Clinic to simply "Brisa Laser Clinic' and need this logo changed to reflect same

Brisa Laser Clinic
Est. 2004

I also need new business cards with above logo included and this attached card changed to the following.
Marianne Holcroft
Dermal Aesthetician
Grad Cert in Laser & IPL Treatments

I need at least one logo in less than 4mb so I can upload into my newsletter format so I can upload to newsletters, emails etc

Thanks
Mari

```html
<!DOCTYPE html>
<html lang="en">
<head>
<meta charset="utf-8">
<title>Brisa Laser Clinic – Business Card</title>
<link rel="stylesheet" href="https://fonts.googleapis.com/css2?family=Source+Sans+3:wght@400;600;700&display=swap">
<style>
  :root {
    --backdrop: #e9eaec;
    --card-green: #00a05e;
    --card-green-light: #06b06a;
    --ink: #ffffff;
    --card-shadow: rgba(0, 0, 0, 0.18);
  }
  * { box-sizing: border-box; margin: 0; padding: 0; }
  html, body {
    width: 1200px;
    height: 864px;
    overflow: hidden;
    background: var(--backdrop);
    font-family: "Source Sans 3", "Myriad Pro", Arial, sans-serif;
  }
  .canvas {
    position: relative;
    width: 1200px;
    height: 864px;
  }
  .business-card {
    position: absolute;
    left: 100px;
    top: 132px;
    width: 1000px;
    height: 600px;
    background: linear-gradient(160deg, var(--card-green-light), var(--card-green) 55%);
    color: var(--ink);
    box-shadow: 0 18px 40px var(--card-shadow);
  }
  .brand {
    position: absolute;
    left: 0;
    right: 0;
    top: 70px;
    text-align: center;
  }
  .brand-name {
    display: block;
    font-size: 140px;
    font-weight: 400;
    line-height: 1;
    letter-spacing: 2px;
  }
  .brand-title {
    display: block;
    margin-top: 36px;
    font-size: 30px;
    font-weight: 600;
    letter-spacing: 9px;
    line-height: 1;
  }
  .brand-est {
    display: block;
    margin-top: 8px;
    font-size: 28px;
    font-weight: 600;
    letter-spacing: 8px;
    line-height: 1;
  }
  .qualification {
    display: block;
    margin-top: 14px;
    font-size: 30px;
    font-weight: 400;
    line-height: 1.1;
  }
  .person {
    position: absolute;
    right: 530px;
    top: 440px;
    text-align: right;
  }
  .person-name {
    font-size: 36px;
    font-weight: 700;
    line-height: 1.1;
  }
  .person-role {
    font-size: 28px;
    font-weight: 400;
    line-height: 1.1;
  }
  .divider {
    position: absolute;
    left: 500px;
    top: 410px;
    width: 3px;
    height: 160px;
    background: var(--ink);
  }
  .contact {
    position: absolute;
    left: 540px;
    top: 408px;
    list-style: none;
    font-size: 27px;
    line-height: 33px;
  }
  .contact-phone { font-weight: 700; }
</style>
</head>
<body>
  <main class="canvas">
    <section class="business-card">
      <header class="brand">
        <span class="brand-name">Brisa</span>
        <span class="brand-title">BRISA LASER CLINIC</span>
        <span class="brand-est">EST. 2004</span>
        <span class="qualification">Grad Cert in Laser &amp; IPL Treatments</span>
      </header>
      <div class="person">
        <p class="person-name">Marianne Holcroft</p>
        <p class="person-role">Dermal Aesthetician</p>
      </div>
      <div class="divider"></div>
      <ul class="contact">
        <li class="contact-phone">(08) 8214 7390</li>
        <li>info@brisaclinic.com.au</li>
        <li>www.brisaclinic.com.au</li>
        <li>512 Wattle Grove Road</li>
        <li>Parkholme SA 5043</li>
      </ul>
    </section>
  </main>
</body>
</html>
```